Marwick Law Letterhead

We need a new letterhead design for a Law Firm. The address for the law firm is 1475 Calloway Street, Suite 210, Houston, Texas 77041. Phone Number: 832-361-9027; Fax Number: 832-614-7359. The logo is uploaded to the project.

```html
<!DOCTYPE html>
<html lang="en">
<head>
<meta charset="utf-8">
<title>Marwick Law Letterhead</title>
<link href="https://fonts.googleapis.com/css2?family=Open+Sans:wght@400;600&family=Roboto:wght@400&display=swap" rel="stylesheet">
<style>
  :root {
    --backdrop: #e4e4e4;
    --paper: #f8f8f8;
    --navy: #1b2a5c;
    --accent-red: #e0232b;
    --body-text: #4a4a4a;
    --contact-text: #2b2b2b;
    --signature-tone: #d9d9d9;
  }
  * { margin: 0; padding: 0; box-sizing: border-box; }
  html, body {
    width: 1153px;
    height: 1200px;
    overflow: hidden;
    background: var(--backdrop);
  }
  .letterhead {
    position: absolute;
    left: 174px;
    top: 40px;
    width: 805px;
    height: 1120px;
    background: var(--paper);
    box-shadow: 0 10px 30px rgba(0,0,0,0.12);
  }
  .brand {
    position: absolute;
    left: 86px;
    top: 92px;
    display: flex;
    align-items: center;
    gap: 14px;
  }
  .brand-mark {
    width: 40px;
    height: 40px;
    background: var(--navy);
  }
  .brand-name {
    font-family: "Open Sans", sans-serif;
    font-weight: 600;
    font-size: 28px;
    color: var(--navy);
    letter-spacing: 0.5px;
  }
  .contact-list {
    position: absolute;
    left: 542px;
    top: 83px;
    list-style: none;
    font-family: "Roboto", sans-serif;
    font-size: 13.5px;
    line-height: 18px;
    color: var(--contact-text);
  }
  .contact-list li {
    display: flex;
    align-items: center;
    gap: 6px;
  }
  .contact-list svg { width: 13px; height: 13px; flex: none; }
  .letter-body {
    position: absolute;
    left: 86px;
    top: 277px;
    width: 633px;
    font-family: "Open Sans", sans-serif;
    font-size: 13.6px;
    line-height: 20.7px;
    color: var(--body-text);
  }
  .letter-body p { margin-bottom: 20.7px; text-align: justify; }
  .letter-body .salutation,
  .letter-body .closing { text-align: left; }
  .signature {
    position: absolute;
    left: 86px;
    top: 829px;
    width: 91px;
    height: 86px;
    background: var(--signature-tone);
  }
  .firm-address {
    position: absolute;
    left: 86px;
    top: 1019px;
    font-family: "Roboto", sans-serif;
    font-style: normal;
    font-size: 13px;
    line-height: 17px;
    color: var(--contact-text);
  }
  .firm-address .firm-name { color: var(--navy); }
</style>
</head>
<body>
  <main class="letterhead">
    <header>
      <div class="brand">
        <span class="brand-mark"></span>
        <span class="brand-name">Marwick Law</span>
      </div>
      <ul class="contact-list">
        <li>
          <svg viewBox="0 0 16 16" aria-hidden="true"><path fill="var(--accent-red)" d="M3.6 1.5 6 4.2 4.7 6a8.5 8.5 0 0 0 5.3 5.3l1.8-1.3 2.7 2.4-1.4 2.1C7.3 14.6 1.4 8.7 1.5 2.9z"/></svg>
          832-361-9027
        </li>
        <li>
          <svg viewBox="0 0 16 16" aria-hidden="true"><rect x="4" y="1" width="8" height="4" fill="var(--accent-red)"/><rect x="1" y="6" width="14" height="6" rx="1" fill="var(--accent-red)"/><rect x="4" y="10" width="8" height="5" fill="var(--accent-red)" stroke="var(--paper)" stroke-width="1"/></svg>
          832-614-7359
        </li>
        <li>
          <svg viewBox="0 0 16 16" aria-hidden="true"><rect x="1" y="3" width="14" height="10" fill="var(--accent-red)"/><path d="M1.5 3.5 8 9l6.5-5.5" fill="none" stroke="var(--paper)" stroke-width="1.2"/></svg>
          info@marwickinjury.com
        </li>
        <li>
          <svg viewBox="0 0 16 16" aria-hidden="true"><circle cx="8" cy="8" r="6.5" fill="none" stroke="var(--accent-red)" stroke-width="1.5"/><path d="M1.5 8h13M8 1.5c-3 3-3 10 0 13M8 1.5c3 3 3 10 0 13" fill="none" stroke="var(--accent-red)" stroke-width="1.2"/></svg>
          www.marwickinjury.com
        </li>
      </ul>
    </header>

    <section class="letter-body">
      <p class="salutation">Dear customer,</p>
      <p>Lorem ipsum dolor sit amet, consectetur adipisicing elit, sed do eiusmod tempor incididunt ut labore et dolore magna aliqua. Ut enim ad minim veniam, quis nostrud exercitation ullamco laboris nisi ut aliquip ex ea commodo consequat. Duis aute irure dolor in reprehenderit in voluptate velit esse cillum dolore eu fugiat nulla pariatur. Excepteur sint occaecat cupidatat non proident, sunt in culpa qui officia deserunt mollit anim id est laborum.</p>
      <p>Lorem ipsum dolor sit amet, consectetur adipisicing elit, sed do eiusmod tempor incididunt ut labore et dolore magna aliqua. Ut enim ad minim veniam, quis nostrud exercitation ullamco laboris nisi ut aliquip ex ea commodo consequat. Duis aute irure dolor in reprehenderit in voluptate velit esse cillum dolore eu fugiat nulla pariatur. Excepteur sint occaecat cupidatat non proident, sunt in culpa qui officia deserunt mollit anim id est laborum.</p>
      <p>Lorem ipsum dolor sit amet, consectetur adipisicing elit, sed do eiusmod tempor incididunt ut labore et dolore magna aliqua. Ut enim ad minim veniam, quis nostrud exercitation ullamco laboris nisi ut aliquip ex ea commodo consequat. Duis aute irure dolor in reprehenderit in voluptate velit esse cillum dolore eu fugiat nulla pariatur. Excepteur sint occaecat cupidatat non proident, sunt in culpa qui officia deserunt mollit anim id est laborum.</p>
      <p>Lorem ipsum dolor sit amet, consectetur adipisicing elit, sed do eiusmod tempor incididunt ut labore et dolore magna aliqua. Ut enim ad minim veniam, quis nostrud exercitation ullamco laboris nisi ut aliquip ex ea commodo consequat. Duis aute irure dolor in reprehenderit.</p>
      <p class="closing">Yours Sincerely,</p>
    </section>

    <div class="signature" role="img" aria-label="Handwritten signature"></div>

    <address class="firm-address">
      <span class="firm-name">Marwick Law</span><br>
      1475 Calloway Street,<br>
      Suite 210, Houston, Texas 77041.
    </address>
  </main>
</body>
</html>
```